"Inkvale" printing shop

-The design must be based around the attached HPID (home page information design) called "Inkvale - HPID".

The table boxes are just for approximate placement of information – you DON'T have to box everything in and you can arrange these. All fonts used in the HPID are only examples - you can use any Google font you wish.

- Information only is in orange text. Copy to go on the design in black text. Some instructions are in the HPID. Please be creative!

-The design needs to be modern. Colours are to be consistent with their new logo or complement it. Keep it clean and simple, you don't need to use lots of colours. Use lots of white.

- images / icons for the site need to be relevant and high quality, but they must also be free images or icons. I have attached a few examples that could be used.

Width of content will be 1100 pixels when implemented as a web page. Header height (without nav bar) 150-200 pixels.

If your design is chosen the winning PSD file will have to be provided as follows…
1. Canvas size of 2000px x 2000px - 72ppi in Adobe Photoshop (CS5 compatible)
2. Width of content section is 1100px wide - centered in the canvas
3. Any button rollovers/hovers in the PSD as hidden layers.
4. All fonts used must be Google fonts.
5. You will need to supply the chosen home page plus one example page (example page as a style guide for how all other pages will look). Example page is only the header and navigational bar at the top, an empty sector in the middle with a column (190 px wide) which can be left or right aligned which means the main sector is 910 pixels wide, and then the footer at the bottom of the page

Checklist - http://pagebuildertally.example/

Examples of some websites that have great design... don't copy them please but they are similar in look to what we are after....
http://www.rookfenly.example/

Industry/Entity Type

Printing

Font styles to use
Serif
Sans Serif

Requirements
Should not have
• Drop shadows, comic sans font

```html
<!DOCTYPE html>
<html lang="en">
<head>
<meta charset="utf-8">
<title>Inkvale – Printing, Laminating &amp; Photocopying</title>
<link rel="stylesheet" href="https://fonts.googleapis.com/css2?family=Open+Sans:ital,wght@0,300;0,400;0,600;0,700;0,800;1,800&display=swap">
<style>
:root{
  --navy:#1e2170;
  --nav:#3a3f91;
  --nav-dark:#2b2f78;
  --ink:#333;
  --muted:#555;
  --white:#fff;
  --blue:#1485d3;
  --magenta:#d7066b;
  --peach:#f8bb78;
  --green:#179a41;
  --violet:#8a7bd6;
  --red:#dc0b1f;
  --orange:#e07b1f;
  --quote-bg:#e9f1f4;
  --footer:#2a2a2a;
}
*{box-sizing:border-box;margin:0;padding:0}
html,body{width:729px;height:1200px;overflow:hidden;background:var(--white)}
body{font-family:"Open Sans",Arial,sans-serif;color:var(--ink);position:relative}

.site-header{position:absolute;left:0;top:0;width:729px;height:72px}
.brand{position:absolute;left:60px;top:21px;display:flex;align-items:center;gap:7px}
.brand-dot{width:30px;height:30px;border-radius:50%;background:var(--navy)}
.brand-name{font-size:22px;font-weight:700;color:var(--navy);line-height:1}
.contact{position:absolute;right:61px;top:22px;text-align:right;padding-right:28px}
.contact-address{font-size:7px;color:var(--muted)}
.contact-phone{font-size:12px;color:var(--navy);margin-top:1px}
.contact-icon{position:absolute;right:0;top:3px;width:22px;height:22px;border-radius:4px;background:#cfcfcf}

.main-nav{position:absolute;left:0;top:72px;width:729px;height:25px;background:linear-gradient(var(--nav),var(--nav-dark))}
.main-nav ul{list-style:none;display:flex;position:absolute;left:60px;top:0;height:25px}
.main-nav li{font-size:6.1px;color:#e4e6f6;padding:0 3.3px;line-height:25px;border-right:1px solid rgba(0,0,0,.25)}
.main-nav li.current{background:var(--navy);color:var(--white);padding:0 6px}

.hero{position:absolute;left:0;top:97px;width:729px;height:303px;overflow:hidden}
.hero-photo{position:absolute;inset:0;background:radial-gradient(ellipse at 35% 45%,#6b6e72 0%,#3f4246 45%,#1f2124 100%)}
.hero-title{position:absolute;left:0;top:38px;width:729px;text-align:center;color:var(--white);line-height:1}
.hero-title span{display:block}
.ht-1{font-size:27px;font-weight:800}
.ht-2{font-size:35px;font-weight:800;margin-top:-2px}
.ht-amp{font-size:60px;font-weight:800;margin-top:-4px}
.ht-3{font-size:35px;font-weight:800;margin-top:-6px}
.ht-4{font-size:24px;font-weight:400;margin-top:2px}
.ht-5{font-size:38px;font-weight:800;font-style:italic}
.hero-arrow{position:absolute;top:140px;width:18px;height:24px;background:rgba(0,0,0,.55)}
.hero-arrow.prev{left:0}.hero-arrow.next{right:0}

.services-title{position:absolute;left:0;top:448px;width:729px;text-align:center;font-size:27px;font-weight:300;color:var(--navy)}
.tile{position:absolute;width:187px;height:114px;display:flex;flex-direction:column;align-items:center;justify-content:center;gap:8px}
.tile svg{width:52px;height:40px}
.tile-label{font-size:11.5px;font-weight:700;color:var(--white);letter-spacing:.2px}
.t-blue{background:var(--blue);left:68px;top:501px}
.t-mag{background:var(--magenta);left:271px;top:501px}
.t-peach{background:var(--peach);left:474px;top:501px}
.t-green{background:var(--green);left:68px;top:631px}
.t-violet{background:var(--violet);left:271px;top:631px}
.t-red{background:var(--red);left:474px;top:631px}

.feature{position:absolute;width:170px}
.feature h3{font-size:11px;font-weight:600;display:flex;align-items:center;gap:5px;margin-left:-14px;white-space:nowrap}
.feature h3 svg{width:9px;height:9px;flex:none}
.feature p{font-size:6.3px;line-height:10.5px;color:var(--muted);margin-top:6px}
.feature a{display:block;font-size:7px;color:#222;margin-top:6px;text-decoration:none}
.f1{left:82px;top:787px;color:var(--blue)}
.f2{left:286px;top:787px;color:var(--magenta)}
.f3{left:490px;top:787px;color:var(--orange)}
.f4{left:82px;top:881px;color:var(--green)}
.f5{left:286px;top:881px;color:var(--violet)}
.f6{left:490px;top:881px;color:var(--red)}

.quote{position:absolute;left:0;top:982px;width:729px;height:135px;background:var(--quote-bg)}
.quote h2{position:absolute;left:85px;top:18px;font-size:17.5px;font-weight:700;color:var(--navy)}
.quote p{position:absolute;left:86px;font-size:7.6px;line-height:12px;color:#222;width:285px}
.quote .q1{top:48px}.quote .q2{top:77px}
.field{position:absolute;background:var(--white);border:1px solid #cfd6da;font-size:6px;color:#888;padding:5px 7px}
.submit{position:absolute;left:601px;top:101px;width:40px;height:18px;background:var(--nav);color:var(--white);font-size:6.3px;text-align:center;line-height:18px}

.site-footer{position:absolute;left:0;top:1117px;width:729px;height:83px;background:var(--footer)}
.footer-links{position:absolute;left:0;top:14px;width:729px;text-align:center;font-size:5.8px;color:#ddd}
.footer-rule{position:absolute;left:60px;top:39px;width:609px;height:1px;background:#444}
.copyright{position:absolute;left:60px;top:56px;font-size:6px;color:#ccc}
.social{position:absolute;top:54px;width:12px;height:12px;border-radius:2px;background:#3c6fb6}
.social.a{left:640px}.social.b{left:656px;background:#3aa6e0}
</style>
</head>
<body>

<header class="site-header">
  <div class="brand"><span class="brand-dot"></span><span class="brand-name">Inkvale</span></div>
  <div class="contact">
    <div class="contact-address">7/28 Harbourside Lane - Westmere - Tauranga</div>
    <div class="contact-phone">07 555 0188</div>
    <span class="contact-icon"></span>
  </div>
</header>

<nav class="main-nav">
  <ul>
    <li class="current">Home</li><li>About</li><li>Photocopying</li><li>Printing</li><li>Laminating</li><li>Business Cards</li><li>Typing Services</li><li>Film Processing</li><li>Photo Printing</li><li>Passport Photos</li><li>Image Restoration</li><li>Printer Supplies</li><li>Free Quote</li><li>Contact</li>
  </ul>
</nav>

<section class="hero">
  <div class="hero-photo" role="img" aria-label="Photo of a digital printing press feeding paper through its rollers"></div>
  <h1 class="hero-title">
    <span class="ht-1">Digital Printing,</span>
    <span class="ht-2">Laminating</span>
    <span class="ht-amp">&amp;</span>
    <span class="ht-3">Photocopying</span>
    <span class="ht-4">Services throughout</span>
    <span class="ht-5">TAURANGA</span>
  </h1>
  <span class="hero-arrow prev"><svg width="18" height="24" viewBox="0 0 18 24"><path d="M11 6 5 12l6 6" fill="none" stroke="#fff" stroke-width="1"/></svg></span>
  <span class="hero-arrow next"><svg width="18" height="24" viewBox="0 0 18 24"><path d="M7 6l6 6-6 6" fill="none" stroke="#fff" stroke-width="1"/></svg></span>
</section>

<h2 class="services-title">OUR SERVICES</h2>

<div class="tile t-blue"><svg viewBox="0 0 52 40"><g fill="none" stroke="#111" stroke-width="2.5" stroke-linejoin="round"><path d="M26 4 4 13l22 9 22-9z"/><path d="M4 20l22 9 22-9"/><path d="M4 27l22 9 22-9"/></g></svg><span class="tile-label">PHOTOCOPYING</span></div>
<div class="tile t-mag"><svg viewBox="0 0 52 40"><g fill="none" stroke="#111" stroke-width="2.5"><rect x="5" y="5" width="42" height="33"/><path d="M12 16h28M12 23h28M12 30h28"/><path d="M11 1v7M18 1v7M25 1v7M32 1v7M39 1v7"/></g></svg><span class="tile-label">LAMINATING &amp; BINDING</span></div>
<div class="tile t-peach"><svg viewBox="0 0 52 40"><g fill="none" stroke="#111" stroke-width="2.5" stroke-linejoin="round"><rect x="2" y="3" width="48" height="34" rx="3"/><path d="M3 5l23 19 23-19M3 35l17-15M49 35 32 20"/></g></svg><span class="tile-label">DIGITAL PRINTING</span></div>
<div class="tile t-green"><svg viewBox="0 0 52 40"><g fill="none" stroke="#111" stroke-width="2.5"><rect x="8" y="2" width="36" height="36" rx="2"/><path d="M16 2v36M36 2v36M16 20h20M8 9h8M8 16h8M8 24h8M8 31h8M36 9h8M36 16h8M36 24h8M36 31h8"/></g></svg><span class="tile-label">FILM PROCESSING</span></div>
<div class="tile t-violet"><svg viewBox="0 0 52 40"><g fill="none" stroke="#111" stroke-width="2.5"><rect x="6" y="4" width="40" height="32" rx="2"/><path d="M13 22h5M21 22h10M13 28h5M21 28h10"/></g></svg><span class="tile-label">BUSINESS CARDS</span></div>
<div class="tile t-red"><svg viewBox="0 0 52 40"><g fill="#111"><path d="M16 2h16l5 5v10H16z"/><rect x="6" y="16" width="40" height="15" rx="2"/><rect x="13" y="26" width="26" height="12" fill="#dc0b1f" stroke="#111" stroke-width="2.5"/></g></svg><span class="tile-label">PHOTO PRINTING</span></div>

<article class="feature f1"><h3><svg viewBox="0 0 10 10"><circle cx="5" cy="5" r="4" fill="none" stroke="currentColor" stroke-width="1.3"/><path d="M3 5l1.5 1.5L7 3.8" fill="none" stroke="currentColor" stroke-width="1.3"/></svg>Cost effective photocopying</h3><p>No matter the quantity of photocopies you need or the size of your copy - you can rely on us to provide a top quality service!</p><a>Click for Photocopying</a></article>
<article class="feature f2"><h3><svg viewBox="0 0 10 10"><circle cx="5" cy="5" r="4" fill="none" stroke="currentColor" stroke-width="1.3"/><path d="M3 5l1.5 1.5L7 3.8" fill="none" stroke="currentColor" stroke-width="1.3"/></svg>All digital format printing</h3><p>Either email us your file or bring it into the store and we can get you the print you need. All prints are to the highest quality.</p><a>Click for Digital Printing</a></article>
<article class="feature f3"><h3><svg viewBox="0 0 10 10"><circle cx="5" cy="5" r="4" fill="none" stroke="currentColor" stroke-width="1.3"/><path d="M3 5l1.5 1.5L7 3.8" fill="none" stroke="currentColor" stroke-width="1.3"/></svg>Laminating and binding</h3><p>Create a professional image for your documents or books. Lamination and binding also keeps your documents well protected!</p><a>Click for Lamination &amp; Binding</a></article>
<article class="feature f4"><h3><svg viewBox="0 0 10 10"><circle cx="5" cy="5" r="4" fill="none" stroke="currentColor" stroke-width="1.3"/><path d="M3 5l1.5 1.5L7 3.8" fill="none" stroke="currentColor" stroke-width="1.3"/></svg>Personal desktop publishing</h3><p>From personalised brochures, posters and birthday and special occasion cards to top quality, cheap business cards - you get it all!</p><a>Click for Desktop Publishing</a></article>
<article class="feature f5"><h3><svg viewBox="0 0 10 10"><circle cx="5" cy="5" r="4" fill="none" stroke="currentColor" stroke-width="1.3"/><path d="M3 5l1.5 1.5L7 3.8" fill="none" stroke="currentColor" stroke-width="1.3"/></svg>Film photo processing</h3><p>Bring in your film to the store and we will work with you to get the best quality print for your purpose and needs. We work with it all!</p><a>Click for Photo Film Processing</a></article>
<article class="feature f6"><h3><svg viewBox="0 0 10 10"><circle cx="5" cy="5" r="4" fill="none" stroke="currentColor" stroke-width="1.3"/><path d="M3 5l1.5 1.5L7 3.8" fill="none" stroke="currentColor" stroke-width="1.3"/></svg>Quality digital photo prints</h3><p>Get your photo printed to your requirements - either from a file or from your digital camera. With a wide range of options you can get the print you want.</p><a>Digital Photo Printing</a></article>

<section class="quote">
  <h2>Get a Free Quote</h2>
  <p class="q1">...or talk to our team about your requirements. Please fill out the form below and we will contact you within a day.</p>
  <p class="q2">You can now upload and send us your file for a free quote!</p>
  <div class="field" style="left:383px;top:23px;width:103px;height:18px">First Name</div>
  <div class="field" style="left:383px;top:49px;width:103px;height:18px">Last Name</div>
  <div class="field" style="left:383px;top:75px;width:103px;height:18px">Phone</div>
  <div class="field" style="left:383px;top:101px;width:103px;height:18px">E-mail</div>
  <div class="field" style="left:492px;top:23px;width:104px;height:96px">First Name</div>
  <div class="submit">SUBMIT</div>
</section>

<footer class="site-footer">
  <div class="footer-links">Home | About | Photocopying | Printing | Laminating | Business cards | Typing services | Film processing | Photo printing | Passport photos | Image restoration | Printer supplies | Dree quote | Contact</div>
  <div class="footer-rule"></div>
  <div class="copyright">Copyright © 2015 &nbsp;Inkvale. &nbsp; All rights reserved.</div>
  <span class="social a"></span><span class="social b"></span>
</footer>

</body>
</html>
```